Ashbrook Pit Advertising / Price List

Create a 1 page document for print and email showcasing what we have available in our Quarry. Bottom of sample should have the information included and then the rest of the document focus on items and services available with the quarry. The top section will need room to list about items below and have about 5 pictures that I am working on getting.

Materials Available for Pick Up and/or Delivery:
Recycled Breaker Run
3/4" & 1 1/4" Crushed Recycled Asphalt
1 1/4" Crushed Recycled Stone
1 1/4" Screened "Dig Right On In"
3/4" Clean Stone
3/8" Washed Pea Stone
Mound Sand
Fill Sand Material
Fill/Clay Fill Material
Compost
Peot Moss
Topsoil
Reclaimed Cream City Bricks

Dumping of Materials with Approval:
Clean Concrete
Dirty and / or Large Concrete or Tolvaran
Clean Brick
Asphalt
Fill Material
Brush and / or Stumps
Hydro Vac Slurry Dumping

Target Market(s)

Contractors in our area

Industry/Entity Type

Trucking & Excavation

Colors
EB3D1F
EC4F4E
F09395
F8D3D4
FCEDEE

Requirements
Must have
• Similar Look & Feel as Sample Copy

```html
<!DOCTYPE html>
<html lang="en">
<head>
<meta charset="utf-8">
<title>Ashbrook Pit – Materials &amp; Services</title>
<link rel="stylesheet" href="https://fonts.googleapis.com/css2?family=Montserrat:wght@700;800&family=Roboto:wght@400;500;700&display=swap">
<style>
  :root {
    --brand-red: #e31e26;
    --page-pink: #fb9a9c;
    --label-pink: #fde6e7;
    --label-shadow: rgba(150, 18, 24, 0.85);
    --ink: #262626;
    --white: #ffffff;
  }
  * { margin: 0; padding: 0; box-sizing: border-box; }
  html, body { width: 848px; height: 1200px; overflow: hidden; background: #ffffff; }
  .flyer {
    position: relative; width: 848px; height: 1200px; overflow: hidden;
    background: var(--page-pink);
    font-family: "Roboto", Arial, sans-serif; color: var(--ink);
  }
  .decor { position: absolute; left: 0; top: 0; width: 848px; height: 1200px; }

  .brand { position: absolute; left: 20px; top: 72px; color: var(--white);
    font-family: "Montserrat", Arial, sans-serif; font-weight: 800; }
  .brand-name { font-size: 29px; letter-spacing: 0.5px; line-height: 1; }
  .brand-tagline { font-size: 5.4px; letter-spacing: 0.2px; margin-top: 8px; }
  .brand-entity { font-size: 10px; margin: 4px 0 0 16px; }
  .brand-town { font-size: 7.5px; margin: 2px 0 0 44px; }

  .section-title { position: absolute; left: 335px; font-size: 16.5px; font-weight: 700; color: var(--ink); }
  .title-materials { top: 16px; }
  .title-dumping { top: 140px; }

  .item-list { position: absolute; list-style: none; font-size: 10.8px; line-height: 14.5px; }
  .item-list li { position: relative; padding-left: 7px; }
  .item-list li::before { content: ""; position: absolute; left: 0; top: 5.5px;
    width: 3.4px; height: 3.4px; border-radius: 50%; background: var(--brand-red); }
  .materials { top: 46px; }
  .materials.col-a { left: 335px; }
  .materials.col-b { left: 520px; }
  .materials.col-b li { padding-left: 14px; }
  .materials.col-c { left: 663px; }
  .materials.col-c li { padding-left: 10px; }
  .dumping { top: 170px; font-size: 10.4px; line-height: 13.6px; }
  .dumping.col-a { left: 335px; }
  .dumping.col-b { left: 525px; }
  .dumping.col-b li { padding-left: 9px; }
  .dumping.col-c { left: 663px; }
  .dumping.col-c li { padding-left: 10px; }

  .service { position: absolute; top: 930px; width: 190px; text-align: center; }
  .service-photo { width: 158px; height: 158px; margin: 0 auto; border-radius: 50%;
    border: 5px solid var(--white); box-shadow: 0 3px 8px rgba(120,20,20,0.35); }
  .service-label { margin-top: 12px; font-size: 18.5px; font-weight: 700; line-height: 19px;
    color: var(--label-pink);
    text-shadow: 0 1px 2px var(--label-shadow), 0 0 6px rgba(190, 30, 40, 0.6); }
  .svc-brush { left: 27px; }
  .svc-excavate { left: 229px; }
  .svc-snow { left: 431px; }
  .svc-trucking { left: 633px; }
  .photo-brush { background: linear-gradient(160deg, #5d4b42 0%, #8b7358 45%, #c9a43a 65%, #7b6b5f 100%); }
  .photo-excavate { background: linear-gradient(180deg, #5f9fd6 0%, #9cc6e8 40%, #c9b04a 55%, #5b4131 75%, #3f2d22 100%); }
  .photo-snow { background: linear-gradient(180deg, #c9cbd2 0%, #8f8a86 40%, #c4a948 52%, #f2f3f6 65%, #ffffff 100%); }
  .photo-trucking { background: linear-gradient(180deg, #4e4a48 0%, #9a9ea6 35%, #6d7f96 50%, #8d6b55 75%, #5a4a40 100%); }

  .contact-bar { position: absolute; left: 0; top: 1149px; width: 848px; height: 51px;
    background: var(--brand-red); color: var(--white);
    font-family: "Montserrat", Arial, sans-serif; font-weight: 700; font-size: 12.5px; line-height: 13px; }
  .contact { position: absolute; top: 12px; }
  .contact-address { left: 61px; top: 10px; }
  .contact-web { left: 281px; }
  .contact-phone { left: 611px; }
  .contact-icon { position: absolute; fill: var(--white); }
  .icon-pin { left: 47px; top: 13px; }
  .icon-mail { left: 266px; top: 14px; }
  .icon-globe { left: 265px; top: 26px; }
  .icon-phone { left: 590px; top: 16px; }
</style>
</head>
<body>
<main class="flyer">
  <svg class="decor" viewBox="0 0 848 1200">
    <defs>
      <linearGradient id="fleetTones" x1="0" y1="0" x2="0" y2="1">
        <stop offset="0" stop-color="#7a6a60"/>
        <stop offset="0.2" stop-color="#6f7e98"/>
        <stop offset="0.36" stop-color="#b8aea3"/>
        <stop offset="0.5" stop-color="#d63a33"/>
        <stop offset="0.75" stop-color="#c9473c"/>
        <stop offset="1" stop-color="#d9d1c5"/>
      </linearGradient>
      <path id="bandCurve" d="M0 845 Q424 990 848 845"/>
    </defs>
    <path class="corner-shape" d="M0 0 H311 C300 150 175 252 0 266 Z" fill="var(--brand-red)"/>
    <path class="arc-top" d="M0 440 Q424 318 848 450 L848 480 Q424 358 0 455 Z" fill="var(--brand-red)"/>
    <path class="fleet-photo" role="img" aria-label="Photo of red roll-off trucks and dumpsters lined up in the quarry yard beside a river"
      d="M0 455 Q424 358 848 480 L848 802 Q424 940 0 802 Z" fill="url(#fleetTones)"/>
    <path class="services-band" d="M0 802 Q424 940 848 802 L848 869 Q424 1005 0 869 Z" fill="var(--brand-red)"/>
    <text font-family="Roboto, Arial, sans-serif" font-weight="700" font-size="34" fill="#ffffff" letter-spacing="0.6">
      <textPath href="#bandCurve" startOffset="50%" text-anchor="middle">Our Commercial and Residential Services Include</textPath>
    </text>
  </svg>

  <header class="brand">
    <div class="brand-name">ASHBROOK PIT</div>
    <div class="brand-tagline">BRUSH CUTTING . EXCAVATING . SNOW REMOVAL . TRUCKING</div>
    <div class="brand-entity">ENTERPRISES, LLC</div>
    <div class="brand-town">ASHBROOK, WI</div>
  </header>

  <h2 class="section-title title-materials">Materials Available for Pick Up and/or Delivery:</h2>
  <ul class="item-list materials col-a">
    <li>Recycled Breaker Run</li>
    <li>3/4" &amp; 1 1/4" Crushed<br>Recycled Asphalt</li>
    <li>1 1/4" Crushed Recycled Stone</li>
    <li>1 1/4" Screened "Dig Right<br>On In"</li>
  </ul>
  <ul class="item-list materials col-b">
    <li>3/4" Clean Stone</li>
    <li>3/8" Washed Pea Stone</li>
    <li>Mound Sand</li>
    <li>Fill Sand Material</li>
    <li>Fill/Clay Fill Material</li>
  </ul>
  <ul class="item-list materials col-c">
    <li>Compost</li>
    <li>Peot Moss</li>
    <li>Topsoil</li>
    <li>Reclaimed Cream<br>City Bricks</li>
  </ul>

  <h2 class="section-title title-dumping">Dumping of Materials with Approval:</h2>
  <ul class="item-list dumping col-a">
    <li>Clean Concrete</li>
    <li>Dirty and / or Large Concrete<br>or Tolvaran</li>
  </ul>
  <ul class="item-list dumping col-b">
    <li>Clean Brick</li>
    <li>Asphalt</li>
    <li>Fill Material</li>
  </ul>
  <ul class="item-list dumping col-c">
    <li>Brush and / or Stumps</li>
    <li>Hydro Vac Slurry</li>
    <li>Dumping</li>
  </ul>

  <section class="service svc-brush">
    <div class="service-photo photo-brush" role="img" aria-label="Photo of a yellow excavator clearing debris"></div>
    <h3 class="service-label">Brush Cutting</h3>
  </section>
  <section class="service svc-excavate">
    <div class="service-photo photo-excavate" role="img" aria-label="Photo of an excavator digging soil under a blue sky"></div>
    <h3 class="service-label">Excavating</h3>
  </section>
  <section class="service svc-snow">
    <div class="service-photo photo-snow" role="img" aria-label="Photo of loaders pushing snow in a parking lot"></div>
    <h3 class="service-label">Snow Plowing and<br>Removal</h3>
  </section>
  <section class="service svc-trucking">
    <div class="service-photo photo-trucking" role="img" aria-label="Photo of a machine sorting demolition debris inside a building"></div>
    <h3 class="service-label">Trucking</h3>
  </section>

  <footer class="contact-bar">
    <svg class="contact-icon icon-pin" width="11" height="17" viewBox="0 0 12 18"><path d="M6 0C2.7 0 0 2.6 0 5.9 0 10.3 6 18 6 18s6-7.7 6-12.1C12 2.6 9.3 0 6 0zm0 8.2A2.3 2.3 0 1 1 6 3.6a2.3 2.3 0 0 1 0 4.6z"/></svg>
    <div class="contact contact-address">1480 Marlow Road<br>Ashbrook, WI 54090</div>

    <svg class="contact-icon icon-mail" width="12" height="9" viewBox="0 0 12 9"><path d="M0 0h12v9H0z" fill="none" stroke="#fff" stroke-width="1.4"/><path d="M0.5 0.8L6 5l5.5-4.2" fill="none" stroke="#fff" stroke-width="1.4"/></svg>
    <svg class="contact-icon icon-globe" width="13" height="13" viewBox="0 0 14 14"><g fill="none" stroke="#fff" stroke-width="1.2"><circle cx="7" cy="7" r="6"/><ellipse cx="7" cy="7" rx="2.6" ry="6"/><path d="M1 7h12M2 4h10M2 10h10"/></g></svg>
    <div class="contact contact-web">dispatch@ashbrookpit.com<br>www.ashbrookpit.com</div>

    <svg class="contact-icon icon-phone" width="16" height="18" viewBox="0 0 16 18"><path d="M3.2 0.6L5.6 0l1.6 4.3-1.9 1.3c.8 2.6 2.5 4.8 4.7 6.2l1.7-1.6 3.9 2.4-.8 2.4c-.5 1.4-2 2.1-3.4 1.6C6 15.1 1.6 9.6.6 4c-.3-1.5.6-3 2.6-3.4z"/></svg>
    <div class="contact contact-phone">Call or Text 555-014-2870<br>Fax 555-014-2871</div>
  </footer>
</main>
</body>
</html>
```